Home Page Design for Motor Manufacturer

Hello,
please design the homepage for a manufacturer of industry motors. I am looking for a professional, clean and minimalistic design. Since this a rather conservative industry it should get a professional look but since it is a redesign there should be some modern that gives is the modern touch of innovation.
A competitor's homepage I like is:
https://www.valdorix.example/en/
What I like about this website:
* clean, minimal, well structured design
* mega menu
For this project please find attached the wireframes (most buttons are in German but by context and Google translate you will easily figure it out; only unclear - "Messe" means "trade exhibition"). The paddings and margins are NOT exact. Also any color of backgrounds etc. chosen is not meant to represent a real color but rather to illustrate the object and maybe show there should be some background emphasis (color or image).
Wireframes:
https: //www.filnest. example / t / pQmW7zKtRb3LyaHx
In both wireframes the only thing that is different is the Service section. I expect from the winner both designs for this service section: one with normal cart design and one with tabs as filters to search products (find image for product categories attached)
In the header use on the left the following text:
h1: "Your competent partner for industrial engines,
-transmission and drawing parts
with more than 5000 satisfied customers "
primary button: Our products
sec. button: Download catalog
and on the right side we feature one or more product images (like putting them in a nice display together).
I also think of a solid background color or subtle gradient for the hero section.
The winner should also design an open mega menu version.
Menu items in this order:
• Home page
• Gearboxes & Motors
• Engine components
• Drawing parts
• Machines & accessories
• About us
• Contact
Also create a language switch with globe symbol and DE for Germany and EN for English above the nav plus the telephone number with icon (user dummy number +49 (0) 987654321)
Output should be in Figma, Sketch or PSD.
Fonts + color to use:
header: Proza Libre, bold, # 0171A1
body: Open Sans, regular, black
Primary accent color: # 0171A1
Text black or dark gray
background: light gray, white or shade of blue
More image resources:
https://www.filnest.example/t/ZuTn4VcqMh8ErwJo
If there are any questions please do not hesitate to ask.
Target Market(s)
B2B - anyone with industrial machinery needing small motors (not car engines)
Industry/Entity Type
Manufacturing
Number of Pages Required
1 page
Requirements
Must have
- see above
Nice to have
- see above
Should not have
- see above

```html
<!DOCTYPE html>
<html lang="en">
<head>
<meta charset="utf-8">
<title>Torvane – Industrial Motors</title>
<link rel="stylesheet" href="https://fonts.googleapis.com/css2?family=Open+Sans:wght@400;600;700&family=Proza+Libre:wght@600;700&display=swap">
<style>
:root{
  --accent:#0171a1;
  --accent-soft:#4d9bc4;
  --card-blue:#2a7fae;
  --orange:#f7860f;
  --ink:#1c1c1c;
  --about-text:#2e6585;
  --section-grey:#f0eeec;
  --footer-grey:#eeedeb;
}
*{box-sizing:border-box;margin:0;padding:0}
html,body{width:1200px;height:3912px;overflow:hidden}
body{position:relative;background:#fff;font-family:"Open Sans",sans-serif;color:var(--ink)}
.abs{position:absolute}

/* top bar */
.topbar{position:absolute;left:0;top:0;width:1200px;height:41px;background:#fff}
.brand{position:absolute;font-family:"Open Sans",sans-serif;font-weight:700;color:var(--accent);letter-spacing:1px}
.topbar .brand{left:26px;top:6px;font-size:22px}
.topbar .contact{position:absolute;top:14px;font-size:10px;color:#222;display:flex;align-items:center;gap:6px}
.nav{position:absolute;left:0;top:41px;width:1200px;height:53px;background:linear-gradient(#f4f4f4,#fafafa)}
.nav ul{list-style:none;position:absolute;left:211px;top:21px;display:flex;gap:23px}
.nav li{font-family:"Proza Libre",sans-serif;font-weight:700;font-size:12px;color:var(--accent)}
.search{position:absolute;left:1003px;top:31px;width:87px;border-bottom:1px solid #9ac0d6}

/* hero */
.hero{position:absolute;left:0;top:117px;width:1200px;height:363px;background:radial-gradient(ellipse at 55% 40%,#41596d 0%,#22384b 45%,#101d29 100%)}
.hero h1{position:absolute;left:120px;top:24px;width:560px;text-align:left;color:#fff;font-weight:400;font-size:32px;line-height:41px}
.hero-display{position:absolute;left:730px;top:22px;width:400px;height:290px;border-radius:12px;background:radial-gradient(ellipse at 50% 55%,#c9d2d9 0%,#7f909e 40%,rgba(40,60,78,.2) 75%)}
.btn-orange{position:absolute;background:var(--orange);color:#fff;font-size:19px;display:flex;align-items:center;justify-content:center}
.btn-ghost{position:absolute;border:2px solid #fff;color:#fff;font-size:19px;display:flex;align-items:center;justify-content:center}

/* features */
.feature{position:absolute;top:445px;width:179px;height:178px;background:var(--card-blue);color:#fff;text-align:center}
.feature svg{position:absolute;left:57px;top:18px}
.feature h3{position:absolute;top:100px;width:100%;font-size:11px;font-weight:600}
.feature p{position:absolute;top:128px;left:14px;right:14px;font-size:9px;line-height:13px}

h2.section-title{position:absolute;font-weight:400;font-size:30px;text-align:center;color:#111}

/* categories */
.cat{position:absolute;top:703px;width:179px;height:113px;background:#efefef;border:1px solid #c9c9c9}
.cat.active{background:var(--accent-soft);border-color:var(--accent-soft)}
.cat .thumb{position:absolute;left:45px;top:14px;width:90px;height:52px;border-radius:6px;background:linear-gradient(90deg,#3a3a3a,#8da4b4,#d6dde2)}
.cat span{position:absolute;top:82px;width:100%;text-align:center;font-size:15px;color:#333}
.cat.active span{color:#fff}

.filter{position:absolute;top:847px;left:219px;width:761px;height:31px;border-bottom:1px solid #bdbdbd;font-size:20px;color:#222}
.filter span{position:absolute;top:0}

.product{position:absolute;background:#fff;border:1px solid #d9d9d9;overflow:hidden}
.product .photo{position:absolute;inset:0}
.product .band{position:absolute;left:0;right:0;bottom:0;height:75px;background:rgba(77,155,196,.93);color:#fff;font-size:20px;display:flex;align-items:center;justify-content:center}
.btn-outline{position:absolute;width:258px;height:67px;border:2px solid #5f9fc6;background:#fff;box-shadow:0 2px 4px rgba(0,0,0,.25);font-size:20px;color:#222;display:flex;align-items:center;justify-content:center}

/* trade */
.trade{position:absolute;left:0;top:1691px;width:1200px;height:1013px;background:var(--section-grey)}
.expo-photo{position:absolute;left:200px;width:275px;height:262px;background:#fff;border:1px solid #8fb3cc}
.expo-photo div{position:absolute;inset:22px 30px;border-radius:8px}
.expo-title{position:absolute;left:589px;font-size:20px;color:#222}
.expo-text{position:absolute;left:589px;width:480px;font-size:15px;line-height:21px;color:#222}
.btn-ticket,.btn-detail{position:absolute;height:54px;display:flex;align-items:center;justify-content:center;font-size:15px;font-weight:700;letter-spacing:.5px}
.btn-ticket{left:589px;width:277px;background:#fff;border:2px solid #8ab9d6;color:var(--accent)}
.btn-detail{left:881px;width:178px;background:#0f6ea0;color:#fff}

/* about */
.about-text{position:absolute;left:728px;top:2770px;width:340px;font-size:17px;line-height:23.4px;color:var(--about-text)}

/* catalogue */
.catalogue{position:absolute;left:0;top:3210px;width:1200px;height:232px;background:linear-gradient(90deg,#223444,#162533 50%,#1f3140)}
.catalogue p{position:absolute;left:608px;top:30px;width:450px;color:#fff;font-size:15px;line-height:21px}

/* contact */
.contact-line{position:absolute;top:3518px;display:flex;align-items:center;gap:10px;font-size:11px;color:#222}

/* footer */
.footer{position:absolute;left:0;top:3597px;width:1200px;height:315px;background:var(--footer-grey)}
.footer .brand{left:126px;top:38px;font-size:24px}
.footer .about{position:absolute;left:126px;top:100px;width:300px;font-size:15px;line-height:23px;color:#222}
.footer h4{position:absolute;top:34px;font-size:16px;font-weight:700;color:#222}
.footer ul{position:absolute;list-style:none;font-size:15px;color:#222}
.footer li{height:32px}
.social{position:absolute;top:44px;width:17px;height:17px;border-radius:50%;background:#1a1a1a}
.copyright{position:absolute;left:126px;top:270px;font-size:13px;color:#222}
</style>
</head>
<body>

<header class="topbar">
  <div class="brand">Torvane</div>
  <div class="contact" style="left:900px">
    <svg width="13" height="13" viewBox="0 0 24 24"><path d="M6.6 10.8a15.1 15.1 0 0 0 6.6 6.6l2.2-2.2a1 1 0 0 1 1-.25 11.4 11.4 0 0 0 3.6.57 1 1 0 0 1 1 1V20a1 1 0 0 1-1 1A17 17 0 0 1 3 4a1 1 0 0 1 1-1h3.5a1 1 0 0 1 1 1c0 1.250.2 2.450.57 3.57a1 1 0 0 1-.25 1z" fill="#111"/></svg>
    +49 (0) 987654321
  </div>
  <div class="contact" style="left:1036px">
    <svg width="13" height="13" viewBox="0 0 24 24" fill="none" stroke="#111" stroke-width="2"><circle cx="12" cy="12" r="10"/><path d="M2 12h20M12 2c3 3 3 17 0 20M12 2c-3 3-3 17 0 20"/></svg>
    DE&nbsp;&nbsp;&nbsp;<span style="color:#555">Switch country ↓</span>
  </div>
</header>

<nav class="nav">
  <ul>
    <li>Home page</li><li>Gearboxes &amp; Motors</li><li>Engine components</li><li>Drawing parts</li><li>Machines &amp; accessories</li><li>About us</li><li>Contact</li>
  </ul>
  <div class="search"></div>
  <svg class="abs" style="left:1095px;top:16px" width="15" height="15" viewBox="0 0 24 24" fill="none" stroke="#0171a1" stroke-width="2.5"><circle cx="10" cy="10" r="7"/><path d="M15 15l6 6"/></svg>
</nav>

<section class="hero" role="img" aria-label="Dark blue close-up photo of industrial gear machinery">
  <h1>Your competent partner for industrial engines, transmission and drawing parts with more than 5000 satisfied customers</h1>
  <div class="btn-orange" style="left:120px;top:214px;width:212px;height:55px">Our Products</div>
  <div class="btn-ghost" style="left:352px;top:214px;width:232px;height:55px">Download catalog</div>
  <div class="hero-display" role="img" aria-label="Display of gear motor and planetary gearbox product photos"></div>
</section>

<div class="feature" style="left:219px">
  <svg width="64" height="70" viewBox="0 0 64 70" fill="none" stroke="#fff" stroke-width="2"><path d="M32 6a12 12 0 0 0-7 22v6h14v-6A12 12 0 0 0 32 6z"/><path d="M27 38h10"/><circle cx="16" cy="46" r="6"/><circle cx="48" cy="46" r="6"/><path d="M4 66c0-8 6-12 12-12s12 4 12 12M36 66c0-8 6-12 12-12s12 4 12 12"/></svg>
  <h3>Innovations</h3><p>Lorem ipsum dolor sit amet, consectetur adipiscing elit, sed do eiusmod tempor</p>
</div>
<div class="feature" style="left:415px">
  <svg width="64" height="70" viewBox="0 0 64 70" fill="none" stroke="#fff" stroke-width="2"><rect x="6" y="4" width="26" height="16" rx="2"/><rect x="32" y="14" width="26" height="16" rx="2"/><circle cx="20" cy="38" r="7"/><circle cx="44" cy="38" r="7"/><path d="M6 64c0-9 6-14 14-14s14 5 14 14M30 64c0-9 6-14 14-14s14 5 14 14M2 66h60"/></svg>
  <h3>Collaboration</h3><p>Lorem ipsum dolor sit amet, consectetur adipiscing elit, sed do eiusmod tempor</p>
</div>
<div class="feature" style="left:609px">
  <svg width="64" height="70" viewBox="0 0 64 70" fill="none" stroke="#fff" stroke-width="2"><rect x="10" y="8" width="44" height="58" rx="3"/><rect x="24" y="3" width="16" height="9" rx="2"/><rect x="16" y="20" width="32" height="38"/><path d="M22 40l7 7 13-15"/></svg>
  <h3>Inspection</h3><p>Lorem ipsum dolor sit amet, consectetur adipiscing elit, sed do eiusmod tempor</p>
</div>
<div class="feature" style="left:804px">
  <svg width="64" height="70" viewBox="0 0 64 70" fill="none" stroke="#fff" stroke-width="2"><path d="M36 38C22 28 18 22 18 15a9 9 0 0 1 18-3 9 9 0 0 1 18 3c0 7-4 13-18 23z"/><path d="M2 50h10l10 6h14a4 4 0 0 1 0 8H22M12 50v14h2l12 4h14l20-14a4 4 0 0 0-6-6l-14 8"/></svg>
  <h3>Support</h3><p>Lorem ipsum dolor sit amet, consectetur adipiscing elit, sed do eiusmod tempor</p>
</div>

<h2 class="section-title" style="left:0;width:1194px;top:644px">Products</h2>

<div class="cat active" style="left:219px"><div class="thumb" role="img" aria-label="Gear motor photo"></div><span>Category 1</span></div>
<div class="cat" style="left:415px"><div class="thumb" role="img" aria-label="Gear motor photo"></div><span>Category 2</span></div>
<div class="cat" style="left:609px"><div class="thumb" role="img" aria-label="Planetary gearbox photo" style="background:linear-gradient(90deg,#c9ced2,#4f84b0,#2c2c2c)"></div><span>Category 3</span></div>
<div class="cat" style="left:804px"><div class="thumb" role="img" aria-label="Planetary gearbox photo" style="background:linear-gradient(90deg,#c9ced2,#6a8fae,#2c2c2c)"></div><span>Category 4</span></div>

<div class="filter">
  <span style="left:141px">Filter:</span>
  <span style="left:243px">All</span>
  <span style="left:289px">|</span>
  <span style="left:323px">Subcategory 1</span>
  <span style="left:484px">|</span>
  <span style="left:515px">Subcategory 2</span>
</div>

<div class="product" style="left:219px;top:910px;width:332px;height:245px"><div class="photo" role="img" aria-label="Harmonic reducer product photo" style="background:radial-gradient(circle at 50% 38%,#7d8388 0%,#bcc1c5 35%,#fff 62%)"></div><div class="band">Product Title</div></div>
<div class="product" style="left:644px;top:910px;width:334px;height:245px"><div class="photo" role="img" aria-label="DC gear motor product photo" style="background:linear-gradient(160deg,#fff 15%,#2b2b2b 40%,#4a4f55 70%,#fff 90%)"></div><div class="band">Product Title</div></div>
<div class="btn-outline" style="left:248px;top:1191px">Details</div>
<div class="btn-outline" style="left:673px;top:1191px">Details</div>

<div class="product" style="left:219px;top:1296px;width:335px;height:244px"><div class="photo" role="img" aria-label="Right-angle gearbox product photo" style="background:linear-gradient(150deg,#b8bcc0 10%,#2b2b2b 45%,#c4c8cc 80%,#fff)"></div><div class="band">Product Title</div></div>
<div class="product" style="left:647px;top:1296px;width:336px;height:244px"><div class="photo" role="img" aria-label="Planetary gearbox product photo" style="background:linear-gradient(120deg,#fff 10%,#c6cbd0 35%,#1f5f9c 60%,#1b1b1b 80%,#fff)"></div><div class="band">Product Title</div></div>
<div class="btn-outline" style="left:248px;top:1577px">Details</div>
<div class="btn-outline" style="left:676px;top:1577px">Details</div>

<section class="trade">
  <h2 class="section-title" style="left:377px;width:600px;top:15px">Trade Exhibition</h2>
</section>

<div class="expo-photo" style="top:1770px"><div role="img" aria-label="Harmonic reducer photo" style="background:radial-gradient(circle,#777d82,#c3c7cb 45%,#fff 70%)"></div></div>
<div class="expo-title" style="top:1788px">Measure Title</div>
<p class="expo-text" style="top:1836px">Lorem Ipsum Dolor Sit Amet, Consectetur Adipiscing Elit, Sed Do Eiusmod Tempor Incididunt Ut Labore Et Dolore Magna Aliqua. Ut Enim Ad Minim Veniam, Quis Nostrud Exercitation Ullamco Laboris Nisi Ut Aliquip Ex Ea Commodo Consequat.</p>
<div class="btn-ticket" style="top:1963px">Free Ticket</div>
<div class="btn-detail" style="top:1963px">Details</div>

<div class="expo-photo" style="top:2075px"><div role="img" aria-label="DC gear motor photo" style="background:linear-gradient(160deg,#fff 10%,#2b2b2b 40%,#50565c 70%,#fff)"></div></div>
<div class="expo-title" style="top:2085px">Measure Title</div>
<p class="expo-text" style="top:2133px">Lorem Ipsum Dolor Sit Amet, Consectetur Adipiscing Elit, Sed Do Eiusmod Tempor Incididunt Ut Labore Et Dolore Magna Aliqua. Ut Enim Ad Minim Veniam, Quis Nostrud Exercitation Ullamco Laboris Nisi Ut Aliquip Ex Ea Commodo Consequat.</p>
<div class="btn-ticket" style="top:2259px">Free Ticket</div>
<div class="btn-detail" style="top:2259px">Details</div>

<div class="expo-photo" style="top:2379px"><div role="img" aria-label="Right-angle gearbox photo" style="background:linear-gradient(150deg,#b8bcc0 10%,#2b2b2b 45%,#c4c8cc 80%,#fff)"></div></div>
<div class="expo-title" style="top:2389px">Measure Title</div>
<p class="expo-text" style="top:2437px">Lorem Ipsum Dolor Sit Amet, Consectetur Adipiscing Elit, Sed Do Eiusmod Tempor Incididunt Ut Labore Et Dolore Magna Aliqua. Ut Enim Ad Minim Veniam, Quis Nostrud Exercitation Ullamco Laboris Nisi Ut Aliquip Ex Ea Commodo Consequat.</p>
<div class="btn-ticket" style="top:2563px">Free Ticket</div>
<div class="btn-detail" style="top:2563px">Details</div>

<h2 class="section-title" style="left:0;width:1200px;top:2650px">About Us</h2>

<div class="abs" role="img" aria-label="Black and white archive photo of a machinist at a lathe" style="left:100px;top:2708px;width:298px;height:379px;background:linear-gradient(160deg,#8a8a8a,#3e3e3e 45%,#6d6d6d 75%,#2a2a2a)"></div>
<div class="abs" role="img" aria-label="Close-up photo of an old engine gear mechanism" style="left:431px;top:2771px;width:275px;height:376px;background:radial-gradient(circle at 50% 45%,#7a6e60,#3b342d 50%,#1c1916)"></div>
<p class="about-text">Lorem Ipsum Dolor Sit Amet, Consectetur Adipiscing Elit, Sed Do Eiusmod Tempor Incididunt Ut Labore Et Dolore Magna Aliqua. Ut Enim Ad Minim Veniam, Quis Nostrud Exercitation Ullamco Laboris Nisi Ut Aliquip Ex Ea Commodo Consequat. Lorem Ipsum Dolor Sit Amet, Consectetur Adipiscing Elit</p>

<section class="catalogue" role="img" aria-label="Dark blue industrial background photo">
  <div class="abs" role="img" aria-label="Open product catalogue brochure" style="left:123px;top:27px;width:371px;height:178px;background:linear-gradient(135deg,#d9dde0,#f4f5f6 50%,#dfe2e4)"></div>
  <p>Lorem Ipsum Dolor Sit Amet, Consectetur Adipiscing Elit, Sed Do Eiusmod Tempor Incididunt Ut Labore Et Dolore Magna Aliqua. Ut Enim Ad Minim Veniam, Quis Nostrud Exercitation Ullamco Laboris Nisi Ut Aliquip Ex Ea Commodo Consequat.</p>
  <div class="btn-orange" style="left:608px;top:147px;width:212px;height:55px">Download</div>
</section>

<h2 class="section-title" style="left:0;width:1200px;top:3478px;font-size:20px">Contact Us</h2>
<div class="contact-line" style="left:320px">
  <svg width="26" height="26" viewBox="0 0 24 24" fill="none" stroke="#0171a1" stroke-width="1.6"><path d="M6.6 10.8a15.1 15.1 0 0 0 6.6 6.6l2.2-2.2a1 1 0 0 1 1-.25 11.4 11.4 0 0 0 3.6.57 1 1 0 0 1 1 1V20a1 1 0 0 1-1 1A17 17 0 0 1 3 4a1 1 0 0 1 1-1h3.5a1 1 0 0 1 1 1c0 1.250.2 2.450.57 3.57a1 1 0 0 1-.25 1z"/></svg>
  +49 (0) 987654321
</div>
<div class="contact-line" style="left:708px">
  <svg width="28" height="22" viewBox="0 0 28 22" fill="none" stroke="#0171a1" stroke-width="1.8"><rect x="1" y="1" width="26" height="20"/><path d="M1 1l13 11L27 1"/></svg>
  contact@torvane-drives.example
</div>

<footer class="footer">
  <div class="brand">Torvane</div>
  <p class="about">Lorem ipsum dolor sit amet, consectetur adipiscing elit, sed do eiusmod tempor incididunt ut labore et dolore.</p>
  <h4 style="left:510px">Company</h4>
  <ul style="left:510px;top:62px">
    <li>Home page</li><li>Gearboxes &amp; Motors</li><li>Engine components</li><li>Drawing parts</li><li>Machines &amp; accessories</li><li>About us</li><li>Contact</li>
  </ul>
  <h4 style="left:735px">Help</h4>
  <ul style="left:735px;top:67px">
    <li>Help center</li><li>Contact support</li><li>Instructions</li><li>How it works</li>
  </ul>
  <span class="social" style="left:971px"></span>
  <span class="social" style="left:1033px"></span>
  <span class="social" style="left:1095px"></span>
  <span class="social" style="left:1157px"></span>
  <p class="copyright">© Copyright 2020. All rights reserved</p>
</footer>

</body>
</html>
```